Automotive Accessories Business Card

Design a business template that match our new logo design and our industry.

https://www.qelmotorgear.com/

Target Market(s)

Aftermarket auto parts and accessories

Industry/Entity Type

automotive

Contact Information for Business Card

company logo

Font styles to use
Serif
Sans Serif

Colors
EB3D1F
EC4F4E
F09395
F8D3D4
FCEDEE

```html
<!DOCTYPE html>
<html lang="en">
<head>
<meta charset="utf-8">
<title>QEL Motor Gear – Business Card</title>
<link href="https://fonts.googleapis.com/css2?family=Montserrat:wght@400;500;700&display=swap" rel="stylesheet">
<style>
  :root {
    --page-bg: #d9d9db;
    --card-bg: #3d3d3f;
    --card-emboss: #343436;
    --accent-red: #e02127;
    --text-light: #ffffff;
    --text-soft: #e6e6e6;
  }
  * { margin: 0; padding: 0; box-sizing: border-box; }
  html, body { width: 1200px; height: 900px; overflow: hidden; }
  body {
    background: var(--page-bg);
    font-family: "Montserrat", Arial, sans-serif;
    position: relative;
  }
  .card {
    position: absolute;
    left: 250px;
    width: 700px;
    height: 400px;
    background: var(--card-bg);
    border-radius: 22px;
    overflow: hidden;
    box-shadow: 0 8px 24px rgba(0,0,0,0.25);
  }
  .card--back { top: 35px; }
  .card--front { top: 465px; }

  .back-brand {
    position: absolute;
    inset: 0;
    display: flex;
    align-items: center;
    justify-content: center;
    gap: 16px;
  }
  .back-brand__mark { width: 34px; height: 34px; background: var(--card-emboss); }
  .back-brand__name {
    font-weight: 700;
    font-size: 50px;
    letter-spacing: 1px;
    color: var(--card-emboss);
  }

  .brand {
    position: absolute;
    top: 70px;
    left: 0; right: 0;
    display: flex;
    align-items: center;
    justify-content: center;
    gap: 14px;
  }
  .brand__mark { width: 26px; height: 26px; background: var(--accent-red); }
  .brand__name {
    font-weight: 700;
    font-size: 40px;
    letter-spacing: 1px;
    color: var(--text-light);
  }

  .person {
    position: absolute;
    top: 195px;
    right: 400px;
    text-align: right;
  }
  .person__name {
    font-weight: 700;
    font-size: 30px;
    letter-spacing: 1px;
    color: var(--accent-red);
    text-transform: uppercase;
  }
  .person__title {
    font-size: 17px;
    color: var(--text-soft);
    margin-top: 2px;
  }

  .divider {
    position: absolute;
    left: 325px;
    top: 170px;
    width: 1px;
    height: 110px;
    background: var(--accent-red);
  }

  .contact-list {
    position: absolute;
    left: 348px;
    top: 172px;
    list-style: none;
  }
  .contact-list li {
    display: flex;
    align-items: center;
    gap: 10px;
    font-size: 16px;
    color: var(--text-soft);
    height: 34px;
  }
  .contact-list svg { width: 15px; height: 15px; fill: var(--accent-red); flex: none; }

  .address {
    position: absolute;
    left: 0; right: 0;
    top: 318px;
    text-align: center;
    font-size: 17px;
    color: var(--text-soft);
    letter-spacing: 0.3px;
  }

  .accent-band {
    position: absolute;
    left: 0; right: 0; bottom: 0;
    height: 14px;
    background: var(--accent-red);
  }
</style>
</head>
<body>

<section class="card card--back" aria-label="Card back">
  <div class="back-brand">
    <span class="back-brand__mark"></span>
    <span class="back-brand__name">QEL MOTOR GEAR INC</span>
  </div>
</section>

<section class="card card--front" aria-label="Card front">
  <div class="brand">
    <span class="brand__mark"></span>
    <span class="brand__name">QEL MOTOR GEAR INC</span>
  </div>

  <div class="person">
    <p class="person__name">Dalen Marsh</p>
    <p class="person__title">CEO/Founder</p>
  </div>

  <span class="divider"></span>

  <ul class="contact-list">
    <li>
      <svg viewBox="0 0 24 24" aria-hidden="true"><path d="M6.6 10.8a15.1 15.1 0 0 0 6.6 6.6l2.2-2.2c.3-.3.7-.4 1-.2 1.1.4 2.3.6 3.6.6.6 0 1 .4 1 1V20c0 .6-.4 1-1 1A17 17 0 0 1 3 4c0-.6.4-1 1-1h3.5c.6 0 1 .4 1 1 0 1.3.2 2.5.6 3.6.1.3 0 .7-.2 1z"/></svg>
      1-866-555-0148
    </li>
    <li>
      <svg viewBox="0 0 24 24" aria-hidden="true"><path d="M2 5h20v14H2z M2 5l10 8 10-8" /><path d="M2 5l10 8 10-8v1.5l-10 8-10-8z" fill="#3d3d3f"/></svg>
      sales@qelmotorgear.com
    </li>
    <li>
      <svg viewBox="0 0 24 24" aria-hidden="true"><circle cx="12" cy="12" r="10"/><path d="M2 12h20M12 2c3 3 3 17 0 20M12 2c-3 3-3 17 0 20" stroke="#3d3d3f" stroke-width="1.5" fill="none"/></svg>
      www.qelmotorgear.com
    </li>
  </ul>

  <p class="address">240 W. Arbor Ave. Suite B Fontana, CA, 92335</p>

  <span class="accent-band"></span>
</section>

</body>
</html>
```